Website Design Request - Management Consulting Firm

We need a Website designed for an IT Management Staffing and Recruiting firm called TRAVENOK based in San Francisco.

The firm is an high-end technology staffing agency. Our focus is on quality and high-caliber candidates rather than quantity.

The website will have two main home pages. One for the recruiter and another on for the candidates.

The website needs to optimize for mobile devices as well.

I have attached few mock-ups that I have done just to show what I am thinking. The UI needs to be very clean, fluid, and it needs to have a modern, rustic, professional feel to it.

Target Market(s)

Technology Manager, Director, VP, CIO of Companies that have $4b-10b dollar revenue. Such as larkspurdwellings.example , https://www.velmorian.example/, quillnet.example, zib.example

Industry/Entity Type

Management Consulting

Number of Pages Required

5+ page

Font styles to use
Sans Serif

Colors
f37122
ffffff

Requirements
Must have
• Please review mock-ups for suggestions
Nice to have
Should not have

```html
<!DOCTYPE html>
<html lang="en">
<head>
<meta charset="utf-8">
<title>TRAVENOK – IT Project Management Jobs</title>
<link rel="stylesheet" href="https://fonts.googleapis.com/css2?family=Montserrat:wght@400;500;600&family=Open+Sans:wght@400;600&display=swap">
<style>
:root{
  --orange:#f37122;
  --white:#ffffff;
  --ink:#3d3d3d;
  --muted:#6f6f6f;
  --soft:#9a9a9a;
  --charcoal:#525252;
  --footer:#f2f2f2;
  --icon:#6a6a6a;
}
*{margin:0;padding:0;box-sizing:border-box}
html,body{width:744px;height:1200px;overflow:hidden;background:var(--white)}
body{position:relative;font-family:"Open Sans",Arial,sans-serif;color:var(--ink)}
.abs{position:absolute}
.heading{font-family:"Montserrat",Arial,sans-serif}

/* header */
.site-header{left:0;top:0;width:744px;height:74px}
.brand{left:69px;top:24px;font-family:"Montserrat",Arial,sans-serif;font-weight:500;font-size:25px;letter-spacing:1px;color:var(--orange);line-height:26px}
.nav a{position:absolute;top:25px;height:25px;line-height:25px;font-size:7.5px;color:var(--ink);text-decoration:none;letter-spacing:.2px}
.nav .active{left:344px;width:50px;border:1px solid var(--orange);border-radius:2px;color:var(--orange);text-align:center}

/* hero */
.hero{left:0;top:74px;width:744px;height:326px;overflow:hidden}
.hero-photo{position:absolute;inset:0;background:
  radial-gradient(ellipse 170px 220px at 640px 130px,#b9b2ab 0%,rgba(185,178,171,0) 70%),
  radial-gradient(ellipse 140px 90px at 680px 300px,#c9ccce 0%,rgba(201,204,206,0) 70%),
  linear-gradient(90deg,#eef0f2 0%,#e8ebee 45%,#dadee1 68%,#c3c8cb 100%)}
.hero-title{left:0;width:744px;top:178px;text-align:center;font-size:19px;font-weight:500;color:#333}
.hero-sub{left:0;width:744px;top:221px;text-align:center;font-size:10px;color:#5a5a5a}
.email-field{left:187px;top:258px;width:236px;height:36px;background:#f4f5f6;border:1px solid #cfd2d4;border-radius:2px;font-size:7px;color:#777;line-height:34px;padding-left:16px}
.cta{left:438px;top:258px;width:119px;height:36px;background:var(--orange);color:var(--white);font-size:7.5px;font-weight:600;text-align:center;line-height:36px;border-radius:2px}
.hero-note{left:0;width:744px;top:310px;text-align:center;font-size:7px;color:#555}
.hero-note span{color:#222;text-decoration:underline;margin-left:4px}
.dots{left:356px;top:377px;width:32px;height:6px}

/* tabs */
.tab{top:443px;height:42px;line-height:42px;text-align:center;color:var(--white);font-size:11.5px;font-weight:500}
.tab-how{left:69px;width:302px;background:var(--orange)}
.tab-why{left:371px;width:303px;background:var(--charcoal)}
.tab-pointer{left:213px;top:485px}

.kicker{left:0;width:744px;top:517px;text-align:center;font-size:7.5px;color:var(--muted)}
.lead{left:0;width:744px;top:537px;text-align:center;font-size:11.5px;color:#444}

/* steps */
.steps{left:0;top:590px;width:744px;height:50px}
.step-art{top:637px;width:96px;height:96px;border-radius:50%}
.art-resume{left:117px;background:radial-gradient(circle at 48% 45%,#fbfbf7 0%,#f3efe2 30%,#e9c66a 44%,#5aace0 62%,#4d9fd4 100%)}
.art-requests{left:323px;background:radial-gradient(circle at 50% 50%,#e96a4f 0%,#3b4a5e 16%,#7fd0c4 34%,#5bbfb0 60%,#4fb3a4 100%)}
.art-bonus{left:530px;background:radial-gradient(circle at 50% 22%,#c9393f 0%,#8fc25b 18%,#3f7c84 42%,#2f6a73 70%,#295f67 100%)}
.step-title{top:752px;width:200px;text-align:center;font-size:10px;font-weight:500;color:#333}
.step-text{top:779px;width:200px;text-align:center;font-size:7px;line-height:16px;color:var(--muted)}
.upload{left:298px;top:842px;width:148px;height:38px;border:1px solid var(--orange);border-radius:2px;text-align:center;line-height:36px;color:var(--orange);font-size:10px;font-weight:500}

/* footer */
.site-footer{left:0;top:958px;width:744px;height:191px;background:var(--footer)}
.footer-head{top:984px;font-size:11.5px;font-weight:500;color:#333}
.footer-brand{left:69px;top:1014px;font-family:"Montserrat",Arial,sans-serif;font-weight:500;font-size:28px;letter-spacing:1px;color:var(--orange);line-height:30px}
.footer-tag{left:69px;top:1048px;font-size:7px;letter-spacing:.6px;color:#333}
.footer-text{font-size:6.5px;line-height:13.6px;color:var(--muted)}
.links{left:358px;top:1008px;list-style:none}
.links li{font-size:6.5px;line-height:16px;color:var(--muted)}
.contact-row{left:522px;font-size:7px;color:#333;display:flex;align-items:center;gap:8px}

.bottom-bar{left:0;top:1149px;width:744px;height:51px}
.copyright{left:68px;top:1170px;font-size:6.5px;color:var(--muted)}
.social{left:600px;top:1168px}
</style>
</head>
<body>

<header class="abs site-header">
  <div class="abs brand">TRAVENOK</div>
  <nav class="nav">
    <a class="active" href="#">HOME</a>
    <a href="#" style="left:415px">PROFESSIONALS</a>
    <a href="#" style="left:507px">EMPLOYERS</a>
    <a href="#" style="left:584px">SIGN IN</a>
    <a href="#" style="left:646px">SIGN UP</a>
  </nav>
</header>

<section class="abs hero">
  <div class="hero-photo" role="img" aria-label="Photo of a professional on a phone call working at a laptop in a bright office"></div>
</section>
<h1 class="abs hero-title heading">Looking for IT Project Management Jobs?</h1>
<p class="abs hero-sub">Upload your resume, accept interview requests, get offers</p>
<div class="abs email-field">Email Address</div>
<div class="abs cta">GET OFFERS NOW</div>
<p class="abs hero-note">Looking for talents? <span>See how it works for Employers</span></p>
<svg class="abs dots" viewBox="0 0 32 6" aria-hidden="true">
  <circle cx="3" cy="3" r="2.6" fill="#9ea3a6"/>
  <circle cx="16" cy="3" r="2.6" fill="#555"/>
  <circle cx="29" cy="3" r="2.6" fill="#9ea3a6"/>
</svg>

<div class="abs tab tab-how heading">How it works?</div>
<div class="abs tab tab-why heading">Why Us?</div>
<svg class="abs tab-pointer" width="14" height="9" viewBox="0 0 14 9" aria-hidden="true"><path d="M0 0H14L7 9Z" fill="#f37122"/></svg>

<p class="abs kicker">3 - simple steps</p>
<h2 class="abs lead heading" style="font-weight:400">Employers pay 25% more for a better FIT Project Manager</h2>

<svg class="abs steps" viewBox="0 0 744 50" aria-hidden="true">
  <g font-family="Montserrat, Arial, sans-serif" font-size="11" fill="#fff" text-anchor="middle">
    <line x1="165" y1="32" x2="165" y2="48" stroke="#888"/>
    <circle cx="165" cy="18" r="14" fill="#4a4a4a"/><text x="165" y="22">1</text>
    <line x1="371" y1="32" x2="371" y2="48" stroke="#888"/>
    <circle cx="371" cy="18" r="14" fill="#4a4a4a"/><text x="371" y="22">2</text>
    <line x1="578" y1="32" x2="578" y2="48" stroke="#888"/>
    <circle cx="578" cy="18" r="14" fill="#4a4a4a"/><text x="578" y="22">3</text>
  </g>
</svg>
<div class="abs step-art art-resume" role="img" aria-label="Illustration of a CV held in hands under a magnifying glass"></div>
<div class="abs step-art art-requests" role="img" aria-label="Illustration of a magnifier searching a network of candidates"></div>
<div class="abs step-art art-bonus" role="img" aria-label="Illustration of a happy professional celebrating a cash bonus"></div>

<h3 class="abs step-title heading" style="left:65px">Upload your Resume</h3>
<h3 class="abs step-title heading" style="left:271px">We send you interview Requests</h3>
<h3 class="abs step-title heading" style="left:478px">Get $1000 Bonus</h3>
<p class="abs step-text" style="left:65px">Answer few questions and upload<br>your resume</p>
<p class="abs step-text" style="left:261px;width:220px">Interested in someone? with a single click, send<br>interview request and let us handle the rest.</p>
<p class="abs step-text" style="left:478px">Find a Job and get $1000 bonus<br>Travenok</p>

<div class="abs upload heading">Upload Your Resume</div>

<footer class="abs site-footer"></footer>
<h4 class="abs footer-head heading" style="left:69px">About</h4>
<h4 class="abs footer-head heading" style="left:358px">Quick Links</h4>
<h4 class="abs footer-head heading" style="left:520px">Contact</h4>
<div class="abs footer-brand">TRAVENOK</div>
<div class="abs footer-tag">PROJECT MANAGEMENT CONSULTING</div>
<p class="abs footer-text" style="left:69px;top:1069px;width:214px">Maecenas scelerisque purus risus, sit amet aliquet dui malesuada vel. Suspendisse libero urna, vestibulum pretium magna id, vulputate auctor metus. Sed porttitor maximus tincidunt. Fusce ultricies est ut ante.</p>
<ul class="abs links">
  <li>About Us</li><li>Services</li><li>How It Works?</li><li>Newsletter</li><li>Contact Us</li><li>Privacy Policy</li><li>Sitemap</li>
</ul>
<p class="abs footer-text" style="left:520px;top:1008px;width:156px;line-height:12.8px">Lorem ipsum dolor sit amet, consectetur adipiscing elit. Nu nc tincidunt, odio eget luctus luctus, sapien magna ultrices ligula, sed lacinia nibh lorem ac mauris.</p>
<div class="abs contact-row" style="top:1073px">
  <svg width="12" height="10" viewBox="0 0 12 10" aria-hidden="true"><rect x="0.5" y="0.5" width="11" height="9" rx="1" fill="#f37122"/><path d="M1 1.5L6 5.5L11 1.5" fill="none" stroke="#fff" stroke-width="1"/></svg>
  info@travenok.example
</div>
<div class="abs contact-row" style="top:1094px">
  <svg width="12" height="12" viewBox="0 0 12 12" aria-hidden="true"><circle cx="6" cy="6" r="5.4" fill="none" stroke="#f37122"/><path d="M4 3.2l1 1.6-.7.8c.4.9 1.1 1.6 2 2l.8-.7 1.6 1-.5 1.1C5.6 9 3 6.4 3 3.7z" fill="#f37122"/></svg>
  555 014 2290
</div>

<div class="abs bottom-bar"></div>
<p class="abs copyright">Copyright © Travenok. All Rights Reserved.</p>
<svg class="abs social" width="72" height="12" viewBox="0 0 72 12" role="img" aria-label="Share, message, email and feed links">
  <g fill="none" stroke="#6a6a6a" stroke-width="1.3" stroke-linecap="round" stroke-linejoin="round">
    <!-- share -->
    <circle cx="2.5" cy="6" r="1.6"/><circle cx="9" cy="2.2" r="1.6"/><circle cx="9" cy="9.8" r="1.6"/>
    <path d="M4 5.2L7.6 3M4 6.8L7.6 9"/>
    <!-- message -->
    <path d="M20 2h10v6.5h-6l-2.5 2.2V8.5H20z"/>
    <!-- email -->
    <rect x="39.5" y="2.5" width="11" height="7.5" rx="1"/>
    <path d="M40 3l5 3.8L50 3"/>
  </g>
  <!-- feed -->
  <g fill="#6a6a6a">
    <circle cx="61.5" cy="9.5" r="1.4"/>
    <path d="M60 5.2a5 5 0 0 1 5.3 5.3h-1.6a3.7 3.7 0 0 0-3.7-3.7z"/>
    <path d="M60 1.6a8.9 8.9 0 0 1 8.9 8.9h-1.6A7.3 7.3 0 0 0 60 3.2z"/>
  </g>
</svg>

</body>
</html>
```